Heron Loan Partners Business Card

We need a business card design for our mortgage servicing company. In addition to servicing the loans of homeowners, we help homeowners with purchasing their homes and any mortgage refinancing. We would like to see designs that use the colors in the logo attached below (gold-ish yellow and navy blue), and any other design you deem fit! The design should communicate a simpler life with smart mortgages provided by Heron.

```html
<!DOCTYPE html>
<html lang="en">
<head>
<meta charset="utf-8">
<title>Heron Loan Partners Business Card</title>
<link rel="stylesheet" href="https://fonts.googleapis.com/css2?family=Open+Sans:wght@400;600;700;800&display=swap">
<style>
  :root {
    --gold: #e0b242;
    --navy: #231f5c;
    --ink: #1c1c1c;
    --paper: #ffffff;
    --backdrop: #222222;
  }
  * { box-sizing: border-box; margin: 0; padding: 0; }
  html, body {
    width: 1200px; height: 780px; overflow: hidden;
    background: var(--backdrop);
    font-family: "Open Sans", sans-serif;
  }
  .stage {
    position: relative; width: 1200px; height: 780px;
    display: flex; align-items: center; justify-content: center; gap: 40px;
  }
  .card {
    position: relative; width: 540px; height: 309px; overflow: hidden;
    box-shadow: 0 10px 24px rgba(0,0,0,.55);
  }
  .card-front { background: var(--gold); display: flex; align-items: center; justify-content: center; }
  .card-back { background: var(--paper); }

  .brand-name {
    font-family: "Open Sans", sans-serif;
    font-weight: 800; color: var(--navy);
    letter-spacing: .5px; line-height: 1.05; text-align: center;
  }
  .card-front .brand-name { font-size: 44px; }
  .card-back .brand-name {
    position: absolute; top: 34px; right: 70px;
    font-size: 26px; text-align: center;
  }

  .accent-bar {
    position: absolute; left: 0; top: 136px;
    width: 16px; height: 50px; background: var(--gold);
  }
  .holder { position: absolute; left: 30px; top: 132px; }
  .holder-name { font-size: 27px; font-weight: 700; line-height: 1.1; white-space: nowrap; }
  .holder-name .first { color: var(--gold); }
  .holder-name .last { color: var(--navy); }
  .holder-title { font-size: 14px; font-weight: 600; color: var(--ink); margin-top: 1px; white-space: nowrap; }

  .address {
    position: absolute; left: 46px; top: 196px;
    font-size: 12.5px; color: var(--ink); line-height: 1.4; white-space: nowrap;
  }

  .contacts { position: absolute; left: 46px; top: 238px; list-style: none; }
  .contacts li {
    display: flex; align-items: center; gap: 8px;
    font-size: 12.5px; color: var(--ink); line-height: 1.4; white-space: nowrap;
  }
  .contacts svg { width: 12px; height: 12px; flex: none; }
</style>
</head>
<body>
<main class="stage">
  <section class="card card-front" aria-label="Card front">
    <div class="brand-name">Heron Loan<br>Partners</div>
  </section>

  <section class="card card-back" aria-label="Card back">
    <div class="brand-name">Heron Loan<br>Partners</div>

    <span class="accent-bar"></span>
    <div class="holder">
      <p class="holder-name"><span class="first">Lena</span> <span class="last">Voskova</span></p>
      <p class="holder-title">Managing Director</p>
    </div>

    <p class="address">1840 Lakeshore Ave. Suite 300<br>Denton, TX 76201</p>

    <ul class="contacts">
      <li>
        <svg viewBox="0 0 24 24" aria-hidden="true"><path fill="var(--gold)" d="M6.6 10.8a15.1 15.1 0 0 0 6.6 6.6l2.2-2.2c.3-.3.7-.4 1-.2 1.1.4 2.3.6 3.6.6.6 0 1 .4 1 1V20c0 .6-.4 1-1 1A17 17 0 0 1 3 4c0-.6.4-1 1-1h3.5c.6 0 1 .4 1 1 0 1.3.2 2.5.6 3.6.1.3 0 .7-.2 1z"/></svg>
        (555) 214-6630
      </li>
      <li>
        <svg viewBox="0 0 24 24" aria-hidden="true"><path fill="var(--gold)" d="M3 5h18a1 1 0 0 1 1 1v12a1 1 0 0 1-1 1H3a1 1 0 0 1-1-1V6a1 1 0 0 1 1-1zm9 7.5L20 7H4z"/></svg>
        info@heronloans.com
      </li>
      <li>
        <svg viewBox="0 0 24 24" aria-hidden="true"><circle cx="12" cy="12" r="9" fill="none" stroke="var(--gold)" stroke-width="2.4"/><path d="M3 12h18M12 3c3 3 3 15 0 18M12 3c-3 3-3 15 0 18" fill="none" stroke="var(--gold)" stroke-width="1.6"/></svg>
        www.heronloans.com
      </li>
    </ul>
  </section>
</main>
</body>
</html>
```